Heritage Hollow Business Cards

Require a business card design. <br/><br/>Needs to include logo (either round or long version) plus these details:<br/>Maya Torvell<br/>Heritage Hollow<br/>maya@kelvadtrading.com.au<br/>02 6481 7395<br/>PO Box Glenwarra NSW 2791<br/>www.heritagehollow.com.au<br/><br/>I need in an editable format so that I can create for multiple staff members. <br/><br/>

Target Market(s)

We are an online store selling renovation products to home owners are builders. Looking for a classic classy design.

Industry/Entity Type

Home And Garden

Contact Information for Business Card

Maya Torvell
Heritage Hollow
maya@kelvadtrading.com.au
02 6481 7395
PO Box Glenwarra NSW 2791
www.heritagehollow.com.au

Colors

Designer to choose colors to be used in the design.

Requirements
Must have
• Must include Logo.

```html
<!DOCTYPE html>
<html lang="en">
<head>
<meta charset="utf-8">
<title>Heritage Hollow Business Cards</title>
<link rel="stylesheet" href="https://fonts.googleapis.com/css2?family=Arimo:wght@400;700&display=swap">
<style>
  :root {
    --backdrop: #8c8c8c;
    --card-white: #ffffff;
    --card-dark: #2a2828;
    --sketch-tone: #1c1b1b;
    --ink: #111111;
    --rule: #9a9a9a;
    --chalk: #e6e6e6;
  }
  * { margin: 0; padding: 0; box-sizing: border-box; }
  html, body { width: 1200px; height: 1200px; overflow: hidden; }
  body {
    background: var(--backdrop);
    font-family: "Arimo", Arial, sans-serif;
    position: relative;
    color: var(--ink);
  }
  .card {
    position: absolute;
    top: 310px;
    width: 366px;
    height: 593px;
    box-shadow: 2px 3px 6px rgba(0,0,0,0.35);
  }
  .card--front { left: 233px; background: var(--card-white); }
  .card--back { left: 627px; background: var(--card-dark); overflow: hidden; }

  .brand {
    position: absolute;
    top: 160px;
    left: 0;
    width: 100%;
    display: flex;
    align-items: center;
    justify-content: center;
    gap: 12px;
  }
  .brand__mark {
    width: 34px; height: 34px;
    border: 1.5px solid var(--ink);
    border-radius: 50%;
  }
  .brand__name { font-size: 29px; font-weight: 400; color: var(--ink); }

  .person {
    position: absolute;
    top: 318px;
    width: 100%;
    text-align: center;
    font-size: 24px;
    font-weight: 700;
    letter-spacing: 0.5px;
  }
  .icon-row {
    position: absolute;
    top: 369px;
    left: 88px;
    width: 190px;
    height: 24px;
    display: flex;
    align-items: center;
    gap: 5px;
  }
  .icon-row__rule { flex: 1; height: 1px; background: var(--rule); }
  .icon-row svg { width: 24px; height: 24px; display: block; }

  .contact {
    position: absolute;
    top: 406px;
    width: 100%;
    text-align: center;
    font-size: 16px;
    line-height: 22px;
  }
  .divider {
    position: absolute;
    top: 484px;
    left: 85px;
    width: 196px;
    height: 1px;
    background: var(--rule);
  }
  .company {
    position: absolute;
    top: 503px;
    width: 100%;
    text-align: center;
    font-size: 16px;
    line-height: 22px;
  }
  .company__name { font-weight: 700; letter-spacing: 0.3px; }

  .back-sketch {
    position: absolute;
    left: 0; top: 250px;
    width: 366px; height: 343px;
    background: linear-gradient(160deg, var(--card-dark) 0%, var(--sketch-tone) 100%);
  }
  .back-badge {
    position: absolute;
    left: 90px; top: 205px;
    width: 184px; height: 184px;
    border: 1.5px solid var(--chalk);
    border-radius: 50%;
    display: flex;
    align-items: center;
    justify-content: center;
    text-align: center;
  }
  .back-badge__name {
    color: var(--chalk);
    font-size: 26px;
    line-height: 28px;
    font-weight: 400;
    margin-top: 40px;
  }
</style>
</head>
<body>
  <section class="card card--front">
    <div class="brand">
      <span class="brand__mark"></span>
      <span class="brand__name">Heritage Hollow</span>
    </div>

    <h1 class="person">MAYA TORVELL</h1>

    <div class="icon-row">
      <span class="icon-row__rule"></span>
      <svg viewBox="0 0 24 24" aria-label="Phone">
        <rect width="24" height="24" rx="4" fill="#111"/>
        <path d="M6 10c0-2 2-3 6-3s6 1 6 3l-2 1-1-2H9l-1 2z" fill="#fff"/>
        <rect x="7" y="12" width="10" height="6" rx="1" fill="#fff"/>
      </svg>
      <svg viewBox="0 0 24 24" aria-label="Email">
        <rect width="24" height="24" rx="4" fill="#111"/>
        <rect x="5" y="7" width="14" height="10" fill="none" stroke="#fff" stroke-width="1.5"/>
        <path d="M5 7l7 6 7-6" fill="none" stroke="#fff" stroke-width="1.5"/>
      </svg>
      <svg viewBox="0 0 24 24" aria-label="Website">
        <rect width="24" height="24" rx="4" fill="#111"/>
        <circle cx="12" cy="12" r="6.5" fill="none" stroke="#fff" stroke-width="1.5"/>
        <path d="M5.5 12h13M12 5.5c-3 3.5-3 9.5 0 13M12 5.5c3 3.5 3 9.5 0 13" fill="none" stroke="#fff" stroke-width="1.2"/>
      </svg>
      <span class="icon-row__rule"></span>
    </div>

    <div class="contact">
      <p>02 6481 7395</p>
      <p>maya@kelvadtrading.com.au</p>
      <p>www.heritagehollow.com.au</p>
    </div>

    <div class="divider"></div>

    <div class="company">
      <p class="company__name">HERITAGE HOLLOW</p>
      <p>PO Box Glenwarra NSW 2791</p>
    </div>
  </section>

  <section class="card card--back">
    <div class="back-sketch" role="img" aria-label="Faint hand-drawn sketch of a roof gable and timber framing"></div>
    <div class="back-badge">
      <p class="back-badge__name">Heritage<br>Hollow</p>
    </div>
  </section>
</body>
</html>
```